Upmarket Dessert Lounge needs a Business Card Design

We are an upmarket dessert lounge needing a business card to match our image.

We want something that is simple yet beautiful, feminine, classy, sophisticated and elegant. We want it to stand out and don't mind if it is bold.

The design should include our logo and colours of red or maroon with gold highlights. We don't mind if black is used.

Marlow & Quince

Target Market(s)

For those who like to indulge or treat themselves and give in to their temptations on good quality desserts.

Industry/Entity Type

Business

Requirements
Must have
• Must include our logo and our name

Marlow & Quince

M & Q

```html
<!DOCTYPE html>
<html lang="en">
<head>
<meta charset="utf-8">
<title>Marlow &amp; Quince — Business Card</title>
<link rel="stylesheet" href="https://fonts.googleapis.com/css2?family=Open+Sans:wght@400;600;700&display=swap">
<style>
  :root {
    --backdrop: #c9c9c9;
    --card-black: #000000;
    --maroon: #7a1315;
    --cream: #fdd49a;
    --white: #ffffff;
    --radius: 28px;
  }
  * { box-sizing: border-box; margin: 0; padding: 0; }
  html, body { width: 956px; height: 1200px; overflow: hidden; }
  body {
    position: relative;
    background: var(--backdrop);
    font-family: "Open Sans", Arial, sans-serif;
  }
  .card {
    position: absolute;
    width: 798px;
    height: 455px;
    background: var(--card-black);
    border-radius: var(--radius);
    overflow: hidden;
    box-shadow: 0 6px 14px rgba(0,0,0,0.35);
  }
  .card--front { left: 79px; top: 98px; }
  .card--back { left: 74px; top: 632px; }

  .card__waves { position: absolute; inset: 0; width: 100%; height: 100%; }

  .brand-name {
    position: absolute;
    color: var(--cream);
    font-weight: 600;
    letter-spacing: 1px;
    white-space: nowrap;
  }
  .card--front .brand-name {
    left: 50px; top: 150px; width: 330px;
    text-align: center;
    font-size: 28px;
  }
  .card--back .brand-name {
    left: 0; right: 0; top: 170px;
    text-align: center;
    font-size: 86px;
    line-height: 1;
  }

  .contact {
    position: absolute;
    left: 432px; top: 80px;
    color: var(--white);
  }
  .contact__name {
    color: var(--cream);
    font-size: 24px;
    font-weight: 700;
    line-height: 1.1;
  }
  .contact__role {
    color: var(--cream);
    font-size: 22px;
    line-height: 1.2;
    margin-bottom: 18px;
  }
  .contact__line { font-size: 18.5px; line-height: 30px; }
  .contact__line b { font-weight: 700; }
  .contact__address { margin-top: 22px; font-size: 18.5px; line-height: 27px; }

  .card__footer {
    position: absolute;
    left: 0; right: 0; top: 410px;
    text-align: center;
    color: var(--white);
    font-size: 18.5px;
  }
  .card__footer b { font-weight: 700; }
  .card__footer .divider { margin: 0 8px; }
</style>
</head>
<body>

  <section class="card card--front">
    <svg class="card__waves" viewBox="0 0 798 455" aria-hidden="true">
      <path fill="var(--maroon)" d="M0 402 C 120 350, 280 360, 420 372 C 520 382, 600 388, 660 372 C 730 352, 780 320, 798 300 L 798 455 L 0 455 Z"/>
      <path fill="var(--card-black)" d="M510 383 C 640 386, 740 330, 798 262 L 798 300 C 760 340, 680 385, 560 385 Z"/>
      <path fill="var(--cream)" d="M524 378 C 650 372, 745 318, 798 240 L 798 262 C 740 330, 640 380, 524 378 Z"/>
    </svg>

    <div class="brand-name">MARLOW &amp; QUINCE</div>

    <div class="contact">
      <div class="contact__name">Your Name</div>
      <div class="contact__role">Designation</div>
      <div class="contact__line"><b>p</b> : 123-456-7890</div>
      <div class="contact__line"><b>c</b> : 123-456-7890</div>
      <div class="contact__line"><b>f</b> : 123-456-7890</div>
      <div class="contact__address">0000, Street Name<br>City Name, Country Code.</div>
    </div>

    <div class="card__footer">
      <b>e</b> : name@yourwebsite.com <span class="divider">|</span> <b>w</b> : www.marlow&amp;quince.com
    </div>
  </section>

  <section class="card card--back">
    <div class="brand-name">M &amp; Q</div>
  </section>

</body>
</html>
```